Reach Crafters Unique Marketing Website Design

I am starting a new company that is a thought leader in the marketing consulting space. The company is called Reach Crafters. We intend to build a Wordpress site on the Astra Theme with the Spectra builder. Our goal is to become the leading voice that empowers high-ticket service business leaders to become Reach Crafters by equipping them with the cutting-edge frameworks and decision grade intelligence taught in leading business schools. What we are looking for is a website design that is clean and professional, making some use of white space well also being eye catching and distinctive in the consulting space. We will probably want to have a video on the homepage not in the hero section, but just below to explain the company and what we do. Our tagline is "Be found. Be chosen." I have attached a brand guide with some messaging, our typography choices, and our color system. The full site will have a primary nav that is four pages - About us, Services, Insights (essentially a blog), and Contact Us. The goal of this project is to develop an art direction that I can give to a designer to build loads of new pages.

Target Market(s)

Business owners (mostly male) from 30-60 years old, looking to fix their sales and marketing funnel.

Industry/Entity Type

Marketing consulting

Font styles to use
Sans Serif

Requirements
Must have
• A clean, professional design that builds trust with owners of high-ticket service businesses. We need a space for explainer video, and sections that tell prospects what we do. Would also like to have a blog carousel.
Nice to have
• Social feeds, if possible. See attached documents for colors and fonts.
Should not have
• Our feel is professional enough to be trustworthy, but unique enough to be memorable. Cartoon ideas do not meet the professional test, and we do not want the website to appear feminine.

```html
<!DOCTYPE html>
<html lang="en">
<head>
<meta charset="utf-8">
<title>Reach Crafters — Be Found. Be Chosen.</title>
<link href="https://fonts.googleapis.com/css2?family=Oswald:wght@300;400;600;700&family=Inter:wght@400;500;600;700&display=swap" rel="stylesheet">
<style>
:root{
  --blue:#2538f2;
  --green:#20ad6a;
  --ink:#161616;
  --text:#3a3a3a;
  --grey-bg:#ececec;
  --footer:#0f0f10;
  --white:#ffffff;
}
*{box-sizing:border-box;margin:0;padding:0}
html,body{width:1200px;height:5329px;overflow:hidden}
body{position:relative;font-family:"Inter",sans-serif;color:var(--text);background:var(--white)}
.abs{position:absolute}
.photo{position:absolute;background:linear-gradient(135deg,#b9c0c8,#7d8791 55%,#4d5660)}
.photo.warm{background:linear-gradient(135deg,#d9d2c8,#9b8c7c 55%,#5c5048)}
.photo.cool{background:linear-gradient(135deg,#d3dbe2,#8fa0ae 55%,#56636e)}
.heading{font-family:"Oswald",sans-serif;font-weight:600;color:var(--ink);text-transform:uppercase;letter-spacing:.5px}
.btn{position:absolute;display:flex;align-items:center;justify-content:center;font-size:15px;font-weight:600;color:var(--white);background:var(--blue);text-decoration:none}
.btn.green{background:var(--green)}
.arrow-btn{position:absolute;width:50px;height:50px;border:2px solid #222;border-radius:50%;display:flex;align-items:center;justify-content:center;background:rgba(255,255,255,.6)}

/* header & hero */
.hero{top:0;left:0;width:1200px;height:672px;background:linear-gradient(90deg,#e9e9ec 0%,#dcdde2 45%,#c9ccd3 100%);overflow:hidden}
.hero-photo{left:470px;top:0;width:730px;height:672px;background:linear-gradient(100deg,rgba(220,221,226,0) 0%,#a9b0ba 30%,#8a939f 60%,#b4bac2 100%)}
.logo{left:143px;top:26px;font-weight:700;font-size:24px;color:var(--ink);letter-spacing:.2px}
.nav{left:567px;top:0;display:flex;height:81px}
.nav a{font-size:15px;font-weight:500;color:var(--ink);text-decoration:none;display:flex;align-items:center;padding:0 0 0 0;margin-right:0}
.nav .active{background:var(--blue);color:var(--white);width:74px;justify-content:center}
.hero-title{left:143px;top:180px;font-family:"Oswald",sans-serif;line-height:1.05}
.hero-title .l1{font-weight:300;font-size:56px;color:var(--ink)}
.hero-title .l2{font-weight:600;font-size:74px;color:var(--blue)}
.hero-copy{left:143px;top:326px;width:390px;font-size:15px;line-height:24px;color:#222}
.dots{display:flex;gap:8px}
.dot{width:12px;height:12px;border-radius:50%;background:#cfd1d6}
.dot.on{background:var(--green)}
.scroll-down{left:572px;top:640px;width:56px;height:56px;border-radius:50%;background:var(--white);box-shadow:0 4px 12px rgba(0,0,0,.15);display:flex;align-items:center;justify-content:center}

/* who we are */
.who{top:672px;left:0;width:1200px;height:704px;background:linear-gradient(180deg,#ffffff 0%,#ffffff 70%,#ececee 100%)}
.who-title{left:621px;top:190px;font-size:50px;font-weight:700}
.who-copy{left:623px;top:260px;width:438px;font-size:15px;line-height:24px;text-align:justify}

/* services */
.services{top:1376px;left:0;width:1200px;height:875px;background:var(--grey-bg)}
.section-title{left:0;width:1200px;text-align:center;font-size:48px;font-weight:700}
.svc-card{position:absolute;width:250px;height:128px;background:var(--white);box-shadow:0 6px 14px rgba(0,0,0,.08);padding:22px 30px}
.svc-card h3{font-size:17px;font-weight:600;color:var(--ink);line-height:25px}
.svc-card a{display:inline-block;margin-top:8px;font-size:17px;font-weight:500;color:var(--green)}

/* video band */
.video-band{top:2251px;left:0;width:1200px;height:583px;background:var(--blue)}
.video{left:143px;top:2108px;width:912px;height:406px;box-shadow:0 20px 30px rgba(0,0,0,.25)}
.play{left:563px;top:2272px;width:74px;height:74px;border-radius:50%;background:var(--green);display:flex;align-items:center;justify-content:center}
.video-title{left:0;top:2580px;width:1200px;text-align:center;color:var(--white);font-size:38px}
.video-copy{left:240px;top:2652px;width:720px;text-align:center;color:var(--white);font-size:15px;line-height:24px}
.video-copy p+p{margin-top:24px}

/* blog */
.blog-card{position:absolute;width:437px}
.blog-card .img{position:relative;height:280px}
.blog-card .row{display:flex;justify-content:space-between;align-items:center;margin-top:22px}
.blog-card h3{font-size:22px;font-weight:600;color:var(--ink)}

/* testimonial */
.client{top:3451px;left:0;width:1200px;height:521px;background:linear-gradient(120deg,#1ea866,#23b36f 50%,#1ba264)}
.client-title{left:0;top:3545px;width:1200px;text-align:center;color:var(--white);font-size:48px}
.quote-mark{left:562px;top:3620px}
.client-quote{left:260px;top:3690px;width:680px;text-align:center;color:var(--white);font-style:italic;font-size:13px;line-height:24px}
.client-name{left:0;top:3780px;width:1200px;text-align:center;color:var(--white);font-size:19px;font-weight:600}
.client-co{left:0;top:3809px;width:1200px;text-align:center;color:var(--white);font-size:14px}
.client .dots{}
.tdot{width:12px;height:12px;border-radius:50%;background:#116b40}
.tdot.on{background:var(--white)}

/* gallery */
.gallery{top:3972px;left:0;width:1200px;height:952px;background:linear-gradient(180deg,#fff 0%,#fff 75%,#e6e6e8 100%)}

/* footer */
.footer{top:4924px;left:0;width:1200px;height:405px;background:var(--footer);color:#cfcfcf}
.f-head{position:absolute;font-size:19px;font-weight:600;color:var(--white)}
.f-head::after{content:"";display:block;width:46px;height:3px;background:var(--green);margin-top:10px}
.f-text{position:absolute;font-size:14px;line-height:24px;color:#bdbdbd}
.f-contact{position:absolute;font-size:13px;line-height:22px}
.f-contact dt{color:var(--white);font-weight:600;display:flex;align-items:center;gap:10px}
.f-contact dd{margin:0 0 12px 24px;color:#bdbdbd}
.social{position:absolute;display:flex;gap:10px}
.social span{width:24px;height:24px;border-radius:50%;background:#3a3a3c}
.social span.on{background:var(--green)}
.f-links{position:absolute;display:flex;gap:26px;font-size:15px;color:var(--white)}
.f-copy{position:absolute;font-size:13px;color:var(--white)}
.f-copy b{color:var(--green)}
</style>
</head>
<body>

<!-- HERO -->
<header class="abs hero">
  <div class="abs hero-photo" role="img" aria-label="Photo of two smiling business professionals holding a tablet and clipboard in a bright office"></div>
  <div class="abs logo">REACH CRAFTERS</div>
  <nav class="abs nav">
    <a class="active" href="#">HOME</a>
    <a href="#" style="margin-left:21px">ABOUT</a>
    <a href="#" style="margin-left:32px">SERVICES</a>
    <a href="#" style="margin-left:30px">INSIGHTS</a>
    <a href="#" style="margin-left:32px">CONTACT</a>
  </nav>
  <h1 class="abs hero-title"><span class="l1">BE FOUND.</span><br><span class="l2">BE CHOSEN.</span></h1>
  <p class="abs hero-copy">Reach Crafters equips high-ticket service firms with decision-grade marketing frameworks to be found, chosen, and trusted — consistently.</p>
  <a class="btn" href="#" style="left:143px;top:410px;width:218px;height:46px">Explore Our Approach</a>
  <a class="btn green" href="#" style="left:371px;top:410px;width:210px;height:46px">Talk to a Reach Crafter</a>
  <div class="abs dots" style="left:143px;top:567px"><span class="dot"></span><span class="dot on"></span><span class="dot"></span><span class="dot"></span></div>
</header>
<div class="abs scroll-down" style="z-index:2">
  <svg width="22" height="22" viewBox="0 0 22 22"><path d="M11 3v15M5 12l6 6 6-6" fill="none" stroke="#222" stroke-width="2"/></svg>
</div>

<!-- WHO WE ARE -->
<section class="abs who">
  <svg class="abs" style="left:0;top:0" width="1200" height="704">
    <path d="M374 176H228v349h146" fill="none" stroke="var(--green)" stroke-width="6"/>
    <path d="M460 331v38" fill="none" stroke="var(--green)" stroke-width="6"/>
  </svg>
  <div class="photo cool" style="left:374px;top:114px;width:199px;height:217px" role="img" aria-label="Photo of a team meeting around a table with laptops"></div>
  <div class="photo" style="left:145px;top:240px;width:198px;height:218px" role="img" aria-label="Photo of colleagues collaborating at a white conference table"></div>
  <div class="photo warm" style="left:374px;top:369px;width:199px;height:217px" role="img" aria-label="Photo of two professionals reviewing a tablet together"></div>
  <h2 class="abs heading who-title">Who We Are</h2>
  <p class="abs who-copy">Lorem ipsum dolor sit amet, consectetur adipiscing elit, sed do eiusmod tempor incididunt ut labore et dolore magna aliqua. Ut enim ad minim veniam, quis nostrud exercitation ullamco laboris nisi ut aliquip ex ea commodo consequat. Duis aute irure dolor in reprehenderit in voluptate velit esse cillum dolore eu fugiat nulla pariatur. Excepteur sint occaecat cupidatat non proident, sunt in culpa qui officia deserunt mollit anim id est laborum.</p>
  <a class="btn" href="#" style="left:623px;top:470px;width:142px;height:48px">Learn More</a>
</section>

<!-- SERVICES -->
<section class="abs services">
  <h2 class="abs heading section-title" style="top:100px">Our Services</h2>
  <div class="photo" style="left:143px;top:192px;width:287px;height:307px" role="img" aria-label="Photo of a strategy workshop with a presenter at a whiteboard"></div>
  <div class="photo cool" style="left:455px;top:192px;width:288px;height:307px" role="img" aria-label="Photo of colleagues celebrating with a high five in an office"></div>
  <div class="photo warm" style="left:770px;top:192px;width:285px;height:307px" role="img" aria-label="Photo of hands reviewing charts and documents on a desk"></div>
  <div class="svc-card" style="left:143px;top:449px"><h3>Demand<br>Strategy</h3><a href="#">Learn More</a></div>
  <div class="svc-card" style="left:455px;top:449px"><h3>Intelligence &amp;<br>Insight</h3><a href="#">Learn More</a></div>
  <div class="svc-card" style="left:770px;top:449px"><h3>Execution<br>Enablement</h3><a href="#">Learn More</a></div>
  <div class="arrow-btn" style="left:49px;top:351px"><svg width="16" height="16" viewBox="0 0 16 16"><path d="M10 3L5 8l5 5" fill="none" stroke="#222" stroke-width="2"/></svg></div>
  <div class="arrow-btn" style="left:1103px;top:351px"><svg width="16" height="16" viewBox="0 0 16 16"><path d="M6 3l5 5-5 5" fill="none" stroke="#222" stroke-width="2"/></svg></div>
  <a class="btn" href="#" style="left:515px;top:612px;width:168px;height:46px">View Services</a>
</section>

<!-- VIDEO -->
<section class="abs video-band"></section>
<div class="photo video" role="img" aria-label="Explainer video still: business team discussing around a meeting table"></div>
<div class="abs play"><svg width="26" height="26" viewBox="0 0 26 26"><path d="M8 5l14 8-14 8z" fill="#fff"/></svg></div>
<h2 class="abs heading video-title">What It Really Takes To Be Chosen</h2>
<div class="abs video-copy">
  <p>Most marketing advice optimizes for noise. We focus on demand — the forces that shape how buyers discover, evaluate, and decide.</p>
  <p>In this short video, we explain how Reach Crafters helps service leaders move from visibility to preference.</p>
</div>

<!-- BLOG -->
<h2 class="abs heading section-title" style="top:2915px">Latest Blog</h2>
<article class="blog-card" style="left:143px;top:3010px">
  <div class="photo cool img" role="img" aria-label="Photo of a tablet showing analytics charts on a desk"></div>
  <div class="row"><h3>Lorem ipsum dolor sit amet</h3><svg width="22" height="22" viewBox="0 0 22 22"><path d="M4 18L18 4M7 4h11v11" fill="none" stroke="var(--blue)" stroke-width="2.5"/></svg></div>
</article>
<article class="blog-card" style="left:619px;top:3010px">
  <div class="photo img" role="img" aria-label="Photo of a presenter leading a boardroom meeting"></div>
  <div class="row"><h3>Lorem ipsum dolor sit amet</h3><svg width="22" height="22" viewBox="0 0 22 22"><path d="M4 18L18 4M7 4h11v11" fill="none" stroke="var(--blue)" stroke-width="2.5"/></svg></div>
</article>
<div class="arrow-btn" style="left:49px;top:3124px"><svg width="16" height="16" viewBox="0 0 16 16"><path d="M10 3L5 8l5 5" fill="none" stroke="#222" stroke-width="2"/></svg></div>
<div class="arrow-btn" style="left:1103px;top:3124px"><svg width="16" height="16" viewBox="0 0 16 16"><path d="M6 3l5 5-5 5" fill="none" stroke="#222" stroke-width="2"/></svg></div>

<!-- CLIENT SAYS -->
<section class="abs client"></section>
<h2 class="abs heading client-title">Client Says</h2>
<svg class="abs quote-mark" width="76" height="56" viewBox="0 0 76 56"><path d="M4 54V32C4 16 12 6 28 2l3 7c-9 3-13 9-13 17h13v28zM44 54V32c0-16 8-26 24-30l3 7c-9 3-13 9-13 17h13v28z" fill="#fff"/></svg>
<p class="abs client-quote">Lorem ipsum dolor sit amet, consectetur adipiscing elit, sed do eiusmod tempor incididunt ut labore et dolore magna aliqua. Ut enim ad minim veniam, quis nostrud exercitation ullamco laboris nisi ut aliquip ex ea commodo consequat.</p>
<div class="abs client-name">John Doe</div>
<div class="abs client-co">Company name</div>
<div class="abs dots" style="left:561px;top:3877px"><span class="tdot"></span><span class="tdot on"></span><span class="tdot"></span><span class="tdot"></span></div>

<!-- GALLERY -->
<section class="abs gallery">
  <h2 class="abs heading section-title" style="top:95px">Gallery</h2>
  <div class="photo warm" style="left:143px;top:185px;width:289px;height:275px" role="img" aria-label="Photo of two colleagues working in a lounge with shelves"></div>
  <div class="photo" style="left:455px;top:185px;width:288px;height:275px;background:linear-gradient(135deg,#5a5550,#3a3632 60%,#2a2725)" role="img" aria-label="Photo of a smiling professional on a phone, social feed preview"></div>
  <div class="photo cool" style="left:766px;top:185px;width:289px;height:275px" role="img" aria-label="Photo of a team gathered around a laptop"></div>
  <div class="photo warm" style="left:143px;top:491px;width:445px;height:275px" role="img" aria-label="Photo of a team meeting seen from behind a presenter"></div>
  <div class="photo cool" style="left:610px;top:491px;width:445px;height:275px" role="img" aria-label="Photo of two professionals discussing a tablet on a staircase"></div>
  <a class="btn" href="#" style="left:505px;top:797px;width:190px;height:48px">View More Photos</a>
</section>

<!-- FOOTER -->
<footer class="abs footer">
  <div class="f-head" style="left:143px;top:94px">About Us</div>
  <p class="f-text" style="left:143px;top:143px;width:345px">Lorem ipsum dolor sit amet, consectetur adip iscing elit, sed do eiusmod tempor incididunt ut labore et dolore magna aliqua. Lorem ipsum dolor sit amet, consectetur</p>
  <div class="social" style="left:145px;top:265px"><span></span><span class="on"></span><span></span></div>

  <div class="f-head" style="left:554px;top:94px">Contact us</div>
  <dl class="f-contact" style="left:554px;top:140px">
    <dt><svg width="12" height="14" viewBox="0 0 12 14"><path d="M6 0a5 5 0 015 5c0 4-5 9-5 9S1 9 1 5a5 5 0 015-5z" fill="var(--green)"/><circle cx="6" cy="5" r="2" fill="#0f0f10"/></svg>Address :</dt>
    <dd>Lorem ipsum dolor sit amet</dd>
    <dt><svg width="14" height="11" viewBox="0 0 14 11"><rect width="14" height="11" fill="var(--green)"/><path d="M0 0l7 6 7-6" fill="none" stroke="#0f0f10" stroke-width="1.5"/></svg>Email Address :</dt>
    <dd>info@companyname.com</dd>
    <dt><svg width="13" height="13" viewBox="0 0 13 13"><path d="M3 0l2 3-1.5 1.5a8 8 0 005 5L10 8l3 2-1.5 3C6 13 0 7 0 1.5z" fill="var(--green)"/></svg>Phone :</dt>
    <dd>+1 888 888 8888</dd>
  </dl>

  <div class="f-head" style="left:809px;top:94px">Newsletter</div>
  <div class="abs" style="left:809px;top:151px;width:246px;height:40px;background:#fff;font-size:12px;color:#777;padding:12px 12px">Email address</div>
  <a class="btn" href="#" style="left:809px;top:207px;width:95px;height:39px;font-size:10px;font-weight:700">SUBSCRIBE</a>

  <nav class="f-links" style="left:143px;top:349px"><span>Home</span><span>About us</span><span>Services</span><span>Insights</span><span>Contact</span></nav>
  <div class="f-copy" style="left:839px;top:351px">© Copyrights 2026 | <b>REACH CRAFTERS</b></div>
</footer>

</body>
</html>
```